Website design with eCommerce for revolutionary new product in the manufacturing industry.

We need a website designed for a precision manufacturing company based in the suburbs of Minneapolis, Minnesota called Velkrin Manufacturing. We have a revolutionary new product, the TARN LOCK, to introduce and sell through an eCommerce storefront. The website would include company information, product information, and the storefront. Green is a color that represents Velkrin Manufacturing. The final design should communicate that we exclusively offer premium products at a premium price. The design should also let the customer know they are the focus of our work.

Target Market(s)

Machinists and machine shops

Industry/Entity Type

Manufacturing and machine shops

Coding

Coded - Design and coding required

Font styles to use
Sans Serif

Colors
59FF00
82FF00
B8FF75
E3FFCB
F4FFEA

Requirements
Must have
• eCommerce storefront, Made in USA references
Nice to have
• Home page, TARN LOCK Product page, About Us, Capabilities, Contact, etc.
Should not have
• Should not be too much text and reading.

```html
<!DOCTYPE html>
<html lang="en">
<head>
<meta charset="utf-8">
<title>Wisdom – TARN LOCK</title>
<link href="https://fonts.googleapis.com/css2?family=Orbitron:wght@700;800;900&family=Poppins:ital,wght@0,400;0,500;0,600;1,400&display=swap" rel="stylesheet">
<style>
:root{
  --green:#59ff00;
  --green-deep:#3fbf00;
  --bg:#141414;
  --bar:#1b1b1b;
  --card:#222222;
  --footer:#0d0d0d;
  --input:#262626;
  --text:#ffffff;
  --muted:#cfcfcf;
}
*{margin:0;padding:0;box-sizing:border-box}
html,body{width:676px;height:1200px;overflow:hidden;background:var(--bg);color:var(--text);font-family:'Poppins',sans-serif}
.page{position:relative;width:676px;height:1200px;overflow:hidden}
.display{font-family:'Orbitron',sans-serif;font-weight:900;letter-spacing:.5px}

.topbar{position:absolute;top:0;left:0;width:676px;height:43px;background:var(--bar)}
.brand{position:absolute;left:50px;top:12px;font-family:'Orbitron',sans-serif;font-weight:900;font-size:15px;color:var(--text);letter-spacing:.5px}
.nav{position:absolute;left:179px;top:0;height:43px;display:flex;align-items:center;gap:11px;font-size:6.6px;font-weight:500;text-transform:uppercase}
.nav .active{color:var(--green)}
.nav-cta{position:absolute;right:0;top:0;width:60px;height:43px;background:var(--green);color:#111;font-size:7px;font-weight:600;display:flex;align-items:center;justify-content:center}

.hero{position:absolute;top:43px;left:0;width:676px;height:220px}
.hero-title{position:absolute;top:68px;width:676px;text-align:center;font-size:35px}

.intro-visual{position:absolute;left:75px;top:287px;width:268px;height:283px}
.intro{position:absolute;left:371px;top:338px;width:260px}
.intro h2{font-size:19px}
.rule{width:48px;height:2px;background:var(--green);margin:8px 0 19px}
.intro h3{font-family:'Orbitron',sans-serif;font-weight:800;font-size:8.5px;letter-spacing:.4px;margin-bottom:11px}
.intro p{font-size:8.4px;line-height:11.2px;color:var(--muted);margin-bottom:9px}

.quotes-head{position:absolute;top:606px;width:676px;text-align:center;font-size:20px}
.quotes-head .rule{margin:8px auto 0}
.arrows{position:absolute;left:559px;top:607px;display:flex;gap:4px}
.arrow-btn{width:27px;height:27px;border-radius:4px;background:#262626;display:flex;align-items:center;justify-content:center}
.arrow-btn.on{background:#3cc400}

.cards{position:absolute;left:62px;top:665px;display:flex;gap:5px}
.card{width:181px;height:140px;background:var(--card);border-radius:8px;text-align:center;padding-top:30px;position:relative}
.card .mark{display:block;margin:0 auto;width:34px;height:20px}
.card blockquote{font-style:italic;font-size:11.5px;line-height:15.5px;color:#d8d8d8;padding:0 12px;margin-top:3px}
.card cite{position:absolute;bottom:18px;left:0;width:100%;font-style:normal;font-family:'Orbitron',sans-serif;font-weight:800;font-size:8.5px;color:var(--green)}

.footer-shape{position:absolute;left:0;top:840px}
.footer-brand{position:absolute;top:942px;width:676px;text-align:center;font-family:'Orbitron',sans-serif;font-weight:900;font-size:19px}
.col{position:absolute;top:1001px}
.col h4{font-family:'Orbitron',sans-serif;font-weight:800;font-size:9px;letter-spacing:.3px;margin-bottom:10px}
.links li{list-style:none;font-size:6.6px;line-height:12.5px}
.links .shop{color:var(--green)}
.social li{list-style:none;font-size:6.8px;display:flex;align-items:center;gap:6px;height:20px}
.social .sq{width:13px;height:13px;background:#232323;border-radius:2px;display:inline-block}
.contact-line{display:flex;gap:6px;font-size:7px;line-height:11px}
.made-usa{margin-top:10px;font-family:'Orbitron',sans-serif;font-weight:800;font-size:7px;color:var(--green);letter-spacing:.3px}
.field{width:145px;height:19px;background:var(--input);border-radius:2px;font-size:6.4px;color:#bbb;padding:0 8px;display:flex;align-items:center;margin-bottom:4px}
.submit{margin-top:5px;width:51px;height:19px;background:#fff;color:#111;font-size:7px;font-weight:600;display:flex;align-items:center;justify-content:center;border-radius:2px}
.divider{position:absolute;left:50px;top:1163px;width:575px;height:1px;background:#2c2c2c}
.copy{position:absolute;top:1177px;width:676px;text-align:center;font-size:7px;font-weight:600}
.to-top{position:absolute;left:635px;top:1151px;width:26px;height:26px;background:var(--green);display:flex;align-items:center;justify-content:center}
</style>
</head>
<body>
<div class="page">

  <header class="topbar">
    <div class="brand">TARN LOCK</div>
    <nav class="nav">
      <span>Why Velkrin Manufacturing?</span>
      <span>What We Do</span>
      <span>How We Make It Better</span>
      <span>Capabilities</span>
      <span>Gallery</span>
      <span>About Us</span>
      <span class="active">Wisdom</span>
    </nav>
    <div class="nav-cta">CONTACT</div>
  </header>

  <section class="hero">
    <svg width="676" height="220" viewBox="0 0 676 220">
      <defs>
        <linearGradient id="metal" x1="0" y1="0" x2="1" y2="1">
          <stop offset="0" stop-color="#8a8580"/>
          <stop offset=".45" stop-color="#5f5a55"/>
          <stop offset="1" stop-color="#7b7066"/>
        </linearGradient>
      </defs>
      <rect width="676" height="220" fill="url(#metal)" role="img" aria-label="Photo of stacked machined aluminium parts"/>
      <polygon points="0,220 676,114 676,143 40,220" fill="var(--green)"/>
      <polygon points="40,220 676,143 676,220" fill="var(--bg)"/>
    </svg>
    <h1 class="hero-title display">WISDOM</h1>
  </section>

  <section>
    <svg class="intro-visual" width="268" height="283" viewBox="0 0 268 283">
      <rect x="50" y="54" width="168" height="168" rx="14" fill="#222" transform="rotate(45 134 138)"/>
      <rect x="70" y="45" width="128" height="210" rx="8" fill="#1e8a12" role="img" aria-label="Render of the green TARN LOCK clamp tool"/>
    </svg>
    <div class="intro">
      <h2 class="display">WISDOM</h2>
      <div class="rule"></div>
      <h3>SHORT AND SWEET ADVICE</h3>
      <p>You didn't come this far, to only come this far.</p>
      <p>Sometimes you come across a great quote that gives you a bit of clarity otherwise not considered. These are a few that we've come across and think are worth sharing.</p>
      <p>If you have one you'd like to see added to the list, let us know!</p>
    </div>
  </section>

  <section>
    <div class="quotes-head display">WORDS OF WISDOM<div class="rule"></div></div>
    <div class="arrows">
      <div class="arrow-btn on"><svg width="12" height="8" viewBox="0 0 12 8"><path d="M11 4H1M4 1 1 4l3 3" stroke="#111" stroke-width="1" fill="none"/></svg></div>
      <div class="arrow-btn"><svg width="12" height="8" viewBox="0 0 12 8"><path d="M1 4h10M8 1l3 3-3 3" stroke="#fff" stroke-width="1" fill="none"/></svg></div>
    </div>
    <div class="cards">
      <article class="card">
        <svg class="mark" viewBox="0 0 34 20"><path d="M4 20 10 0h7L12 20ZM19 20 25 0h7L27 20Z" fill="#2f8f10"/></svg>
        <blockquote>Sometimes the shortcut is the long way.</blockquote>
        <cite>- JAPANESE WISDOM</cite>
      </article>
      <article class="card">
        <svg class="mark" viewBox="0 0 34 20"><path d="M4 20 10 0h7L12 20ZM19 20 25 0h7L27 20Z" fill="#2f8f10"/></svg>
        <blockquote>No problem can withstand the assault of sustained thinking.</blockquote>
        <cite>- FORTUNE COOKIE</cite>
      </article>
      <article class="card">
        <svg class="mark" viewBox="0 0 34 20"><path d="M4 20 10 0h7L12 20ZM19 20 25 0h7L27 20Z" fill="#2f8f10"/></svg>
        <blockquote>If you're picky, you go without.</blockquote>
        <cite>- GRANDPA</cite>
      </article>
    </div>
  </section>

  <footer>
    <svg class="footer-shape" width="676" height="360" viewBox="0 0 676 360"><polygon points="0,108 676,4 676,360 0,360" fill="var(--footer)"/></svg>
    <div class="footer-brand">TARN LOCK</div>

    <div class="col" style="left:81px">
      <h4>HELPFUL LINKS</h4>
      <ul class="links">
        <li>Why Velkrin Manufacturing?</li><li>What We Do</li><li>How We Make It Better</li><li>Capabilities</li><li>Gallery</li><li>About Us</li><li>Wisdom</li><li>Contact Us</li><li class="shop">Shop TARN LOCK</li>
      </ul>
    </div>
    <div class="col" style="left:216px">
      <h4>INFORMATION</h4>
      <ul class="social">
        <li><span class="sq"></span>Facepage</li>
        <li><span class="sq"></span>Chirper</li>
        <li><span class="sq"></span>Searchly</li>
        <li><span class="sq"></span>Workline</li>
        <li><span class="sq"></span>Vidcast</li>
      </ul>
    </div>
    <div class="col" style="left:330px">
      <h4>CONTACT US</h4>
      <div class="contact-line">
        <svg width="8" height="6" viewBox="0 0 8 6" style="margin-top:3px"><rect width="8" height="6" fill="var(--green)"/><path d="M0 0l4 3 4-3" stroke="#111" stroke-width=".8" fill="none"/></svg>
        <div>Email:<br>hello@tarnlock-mfg.com</div>
      </div>
      <div class="made-usa">MADE IN USA</div>
    </div>
    <div class="col" style="left:450px">
      <h4>GET IN TOUCH</h4>
      <div class="field">Enter Name</div>
      <div class="field">Enter Company</div>
      <div class="field">Enter Country</div>
      <div class="submit">SUBMIT</div>
    </div>

    <div class="divider"></div>
    <div class="copy">© COPYRIGHT 2022 TARN LOCK, ALL RIGHTS RESERVED</div>
    <div class="to-top"><svg width="8" height="10" viewBox="0 0 8 10"><path d="M4 10V1M1 4l3-3 3 3" stroke="#111" stroke-width="1" fill="none"/></svg></div>
  </footer>

</div>
</body>
</html>
```